A business card design for a dental office. We have Two doctors working here. We practice general de

I already have a logo designed for the office with the name and a slogan.
Now I need to create design for a business card using the same logo.
Details Needed on the front side of the card are :
Bernard K. Oswin, DDS
Gerald M Fenwick, DDS
418 Birch Lane
Kestrel Bay, ZZ 00000
Phone : 555 019 4831
Fax : 555 019 4832
Website : WWW.BrightmoorToothHaven.Com
Office hours by appointment
On the back side of the card need :
Appointment
Date....................Time...................
With....................................
If unable to keep your appointment, please give 24-48 hours notice in order to avoid broken appointment fee.

Industry/Entity Type

Dental Clinic

Contact Information for Business Card

Bernard K. Oswin, DDS
Gerald M Fenwick, DDS
418 Birch Lane
Kestrel Bay, ZZ 00000
Phone : 555 019 4831
Fax : 555 019 4832
Appointment

Requirements
Must have
• Keep the Name and slogan on the logo on the front of the card. You can move them around the Logo and Name/Slogan of business (Oswin Family Dentistry/Gentle care for every smile) as you wish to get a feel of the design.
• Bernard K. Oswin, DDS
• Gerald M Fenwick, DDS
• 418 Birch Lane
• Kestrel Bay, ZZ 00000
• Phone : 555 019 4831
• Fax : 555 019 4832
• WWW.BrightmoorToothHaven.Com
• Keep these three groups above as they are together now in different areas of the front side.
• On the back side of the card need :
• Appointment
• Date....................Time...................
• With....................................
• If unable to keep your appointment, please give 24-48 hours notice in order to avoid broken appointment fee.

```html
<!DOCTYPE html>
<html lang="en">
<head>
<meta charset="utf-8">
<title>Oswin Family Dentistry – Business Card</title>
<link rel="stylesheet" href="https://fonts.googleapis.com/css2?family=Arimo&family=Cinzel:wght@700;900&family=PT+Sans:wght@700&display=swap">
<style>
  :root {
    --brand-blue: #0b54a6;
    --brand-orange: #f0732a;
    --brand-red: #e03a2c;
    --ink: #1b1b1b;
    --paper: #ffffff;
    --backdrop: #e6e6e3;
  }
  * { margin: 0; padding: 0; box-sizing: border-box; }
  html, body { width: 1189px; height: 1200px; overflow: hidden; }
  body { background: var(--backdrop); position: relative; }

  .card {
    position: absolute; left: 136px; width: 917px; height: 524px;
    background: var(--paper); overflow: hidden;
    box-shadow: 0 3px 10px rgba(0,0,0,.25);
  }
  .card--front { top: 45px; }
  .card--back { top: 623px; }

  .card__waves { position: absolute; inset: 0; width: 100%; height: 100%; }

  .brand-mark {
    position: absolute; left: 80px; top: 41px; width: 172px; height: 172px;
    border-radius: 50%; background: var(--brand-blue);
  }
  .brand-name {
    position: absolute; left: 287px; top: 106px;
    font: 700 42px/1 "PT Sans", sans-serif; letter-spacing: 3px;
    color: var(--brand-blue); white-space: nowrap;
  }
  .brand-slogan {
    position: absolute; left: 341px; top: 166px; width: 466px;
    display: flex; align-items: center; gap: 12px;
    font: 700 16px/1 "PT Sans", sans-serif; letter-spacing: 3.2px;
    color: var(--brand-red); white-space: nowrap;
  }
  .brand-slogan::before, .brand-slogan::after {
    content: ""; flex: 1; height: 1px; background: var(--brand-red);
  }

  .doctors { position: absolute; left: 38px; top: 336px; color: var(--paper); }
  .doctor { font: 700 29px/1.1 "Cinzel", serif; letter-spacing: 3px; margin-bottom: 24px; }
  .doctor span { display: block; }

  .contact { position: absolute; left: 411px; top: 325px; list-style: none; }
  .contact li {
    display: flex; align-items: center; height: 44px;
    font: 26px/1 "Arimo", sans-serif; color: var(--paper); white-space: nowrap;
  }
  .contact__icon {
    width: 19px; height: 19px; background: var(--brand-orange);
    margin-right: 24px; flex: none;
  }

  .appt-title {
    position: absolute; left: 0; right: 0; top: 76px; height: 48px;
    display: flex; align-items: center; gap: 12px;
    font: 900 43px/1 "Cinzel", serif; letter-spacing: 2px; color: var(--brand-blue);
  }
  .appt-title::before, .appt-title::after {
    content: ""; height: 2px; background: var(--brand-red); flex: 1;
  }
  .appt-title::after { flex: 0.8; }

  .weekdays { position: absolute; left: 0; top: 168px; width: 100%; }
  .weekday {
    position: absolute; transform: translateX(-50%); text-align: center;
    font: 28px/1 "Arimo", sans-serif; color: var(--ink);
  }
  .weekday__box {
    display: block; width: 43px; height: 41px; margin: 20px auto 0;
    border: 1px solid #555;
  }

  .field {
    position: absolute; font: 28px/1 "Arimo", sans-serif; color: var(--ink); white-space: nowrap;
  }
  .field-line { position: absolute; height: 3px; background: var(--ink); }
</style>
</head>
<body>

<section class="card card--front">
  <svg class="card__waves" viewBox="0 0 1123 642" preserveAspectRatio="none" aria-hidden="true">
    <path d="M0,305 C300,395 620,365 820,290 C910,258 1010,258 1123,330 L1123,340 C1020,285 920,280 830,305 C610,385 300,400 0,372 Z" fill="var(--brand-orange)"/>
    <path d="M0,378 C300,410 620,380 835,305 C935,272 1040,280 1123,355 L1123,642 L0,642 Z" fill="var(--brand-blue)"/>
  </svg>

  <div class="brand-mark"></div>
  <h1 class="brand-name">OSWIN FAMILY DENTISTRY</h1>
  <p class="brand-slogan">GENTLE CARE FOR EVERY SMILE</p>

  <div class="doctors">
    <p class="doctor"><span>Bernard K. Oswin</span><span>DDS</span></p>
    <p class="doctor"><span>Gerald M Fenwick</span><span>DDS</span></p>
  </div>

  <ul class="contact">
    <li><span class="contact__icon"></span>555 019 4831</li>
    <li><span class="contact__icon"></span>555 019 4832</li>
    <li><span class="contact__icon"></span>WWW.BrightmoorToothHaven.Com</li>
    <li><span class="contact__icon"></span>418 Birch Lane Kestrel Bay, ZZ 00000</li>
  </ul>
</section>

<section class="card card--back">
  <h2 class="appt-title">Appointment</h2>

  <div class="weekdays">
    <div class="weekday" style="left:165px">MON<span class="weekday__box"></span></div>
    <div class="weekday" style="left:261px">TUE<span class="weekday__box"></span></div>
    <div class="weekday" style="left:363px">WED<span class="weekday__box"></span></div>
    <div class="weekday" style="left:462px">THU<span class="weekday__box"></span></div>
    <div class="weekday" style="left:559px">FRI<span class="weekday__box"></span></div>
    <div class="weekday" style="left:656px">SAT<span class="weekday__box"></span></div>
    <div class="weekday" style="left:756px">SUN<span class="weekday__box"></span></div>
  </div>

  <span class="field" style="left:47px;top:314px">Date :-</span>
  <span class="field-line" style="left:150px;top:330px;width:248px"></span>
  <span class="field" style="left:414px;top:314px">Time :-</span>
  <span class="field-line" style="left:513px;top:330px;width:249px"></span>
  <span class="field" style="left:773px;top:312px">am/pm</span>

  <span class="field" style="left:47px;top:382px">Date :-</span>
  <span class="field-line" style="left:150px;top:398px;width:248px"></span>
  <span class="field" style="left:414px;top:382px">Time :-</span>
  <span class="field-line" style="left:513px;top:398px;width:249px"></span>
  <span class="field" style="left:773px;top:380px">am/pm</span>

  <span class="field" style="left:262px;top:451px">With :-</span>
  <span class="field-line" style="left:362px;top:466px;width:249px"></span>
</section>

</body>
</html>
```